Etiketten-Design für Dankeswein
Zielgruppe
Kelvora:
Wir stellen für unsere Kunden einen Dankeswein her. Er soll eine Hommage an die Freundschaft und Partnerschaft sein.
Subtitle, could be, but perhaps not:
When we meet, anything can happen.
Name: Kelvora (evtl. Änderung auf Tarnis)
Aufgabenstellung
Das Ettikett darf auch bunt sein, aber es sollte vorallem sehr Professionell sein.
Der Wein wird rötlich sein, die Flasche weiss durchsichtig. Es werden wahrscheinlich 0,5l Flaschen.
Die Form des Ettikets, kann noch definiert werden.
Es geht um eine Homage an das Treffen von Menschen und die Freundschaft.
Kelvora
Hintergrundinfos, die eher für den Hintergrund, Einarbeitung und kleine Abbildung gedacht sind.
PLORAX: ist eine IT Firma, die von 2 Partnern gegründet wurde. Das Logo sollte mit drauf, evtl. kann man auch sich an diesen Farben orientieren.
Familie Dormak: Die Tiersymbole repräsentieren die beiden Eltern. Das geschwungene H ist das Familienzeichen. Wenn man es rotiert. ähnelt es wieder einem Schmetterling. Vielleicht kann man da grafisch etwas machen?
Das geschwungene H oder die Tiersymbole haben hohen emotionalen Wert. In dem Wappen ist das neue Familiensymbol eingearbeitet in das noch ältere Familienwappen der Familie. Prio hat das geschwungene H
Für das Ettikett gibt es leider rechtliche Pflichtangaben:
PLORAX GmbH
Lindauring 14 CH-4057 Basel
Erzeugerab füllung:D- RP 7 348 962
A.P.-Nr.7 348 962 XXXX
11,0%vol 50 cl Enthält Sulfite
Deutscher Qualitätswein – Mosel
kelvora-beispiel.eu

```html
<!DOCTYPE html>
<html lang="de">
<head>
<meta charset="utf-8">
<title>Tarnis – Rotling 2020 Etikett</title>
<link rel="stylesheet" href="https://fonts.googleapis.com/css2?family=Cinzel:wght@700&family=Montserrat:wght@300;500;700&display=swap">
<style>
  :root {
    --page-bg: #ecebea;
    --label-white: #ffffff;
    --label-black: #000000;
    --gold: #b9a44c;
    --gold-soft: #d8c98a;
    --ink-white: #ffffff;
    --mono-tone: #1a1a1a;
  }
  html, body {
    margin: 0;
    width: 848px;
    height: 1200px;
    overflow: hidden;
    background: var(--page-bg);
  }
  .canvas {
    position: relative;
    width: 848px;
    height: 1200px;
  }
  .label {
    position: absolute;
    left: 124px;
    top: 285px;
    width: 600px;
    height: 631px;
    box-shadow: 0 2px 10px rgba(0,0,0,0.12);
  }
  .label__head {
    position: absolute;
    inset: 0 0 auto 0;
    height: 150px;
    background: var(--label-white);
  }
  .family-mark {
    position: absolute;
    left: 184px;
    top: 26px;
    width: 207px;
    height: 106px;
    border-radius: 50px;
    background: linear-gradient(90deg, #e6e6e6, #cfcfcf 50%, #e6e6e6);
  }
  .label__panel {
    position: absolute;
    left: 0;
    top: 150px;
    width: 600px;
    height: 481px;
    background: var(--label-black);
    text-align: center;
  }
  .wine-name {
    position: absolute;
    left: 0;
    right: 0;
    top: 24px;
    margin: 0;
    font-family: "Cinzel", serif;
    font-weight: 700;
    font-size: 74px;
    line-height: 1;
    letter-spacing: 1px;
    color: var(--gold);
  }
  .grape-art {
    position: absolute;
    left: 236px;
    top: 118px;
    width: 124px;
    height: 156px;
    border-radius: 40% 40% 50% 50%;
    background: radial-gradient(circle at 45% 55%, var(--gold-soft), var(--gold) 70%);
  }
  .vintage {
    position: absolute;
    left: 0;
    right: 0;
    top: 306px;
    margin: 0;
    font-family: "Montserrat", sans-serif;
    font-weight: 700;
    font-size: 30px;
    letter-spacing: 5px;
    color: var(--ink-white);
  }
  .variety {
    position: absolute;
    left: 0;
    right: 0;
    top: 352px;
    margin: 0;
    font-family: "Montserrat", sans-serif;
    font-weight: 300;
    font-size: 32px;
    letter-spacing: 7px;
    color: var(--ink-white);
  }
  .producer {
    position: absolute;
    left: 0;
    right: 0;
    top: 418px;
    margin: 0;
    font-family: "Montserrat", sans-serif;
    font-weight: 500;
    font-size: 30px;
    letter-spacing: 1px;
    color: var(--ink-white);
  }
</style>
</head>
<body>
  <main class="canvas">
    <section class="label">
      <header class="label__head">
        <div class="family-mark" role="img" aria-label="Geschwungenes H – Familienzeichen der Familie Dormak"></div>
      </header>
      <div class="label__panel">
        <h1 class="wine-name">Tarnis</h1>
        <div class="grape-art" role="img" aria-label="Goldene Weintraube mit Blatt und Ranke"></div>
        <p class="vintage">2020</p>
        <p class="variety">ROTLING</p>
        <p class="producer">PLORAX</p>
      </div>
    </section>
  </main>
</body>
</html>
```